Recruitment Agency Needs a Core Values Wall for Office

Hello! We are hoping to reach out to the designer community to help us with achieving a wall in our office that beautifully presents our core values, so thanks for stopping by!
We are in a corporate office, but our median age in the office is 28 years old. For this reason we want the design to be fun, young and colourful while showing some sophistication.
The wall will be visible to the staff (within the open plan office), and the right colours will need to be used to enhance mood and productivity. Perhaps we could be looking at a colour for each core value? Or potentially some other way for each value to stand out?
The background doesn't have to be a specific colour. We would like some options to see how it will reflect in the office.
In terms of size - we aren't 100% on what size we are wanting to do it... but work within 1500x2700mm and we can work off that.
Fonts can be experimented with, without being too overpowering to the eye.
It needs to be clear, punchy and stand out from across the office (while being easy on the eye).
I have attached two images that can be used as inspiration. We would like more colour throughout the design.
The core values that will be required to be displayed:
Stop. Think. Challenge the Norm.
Our Detail is Our Difference.
Best Intentions. ALWAYS.
Turn Up, Turn On! Make ..it Happen!
Support Like Family. Party Like Rockstars.
Median staff age of 28, corporate office
Recruitment

```html
<!DOCTYPE html>
<html lang="en">
<head>
<meta charset="utf-8">
<title>Core Values Wall</title>
<link rel="stylesheet" href="https://fonts.googleapis.com/css2?family=Stardos+Stencil:wght@700&family=Cinzel:wght@400&family=Anton&family=Alfa+Slab+One&family=Share+Tech&family=Lobster&family=Sancreek&family=Rye&display=swap">
<style>
  :root {
    --paper: #efefef;
    --teal: #4a8a77;
    --apricot: #f5a854;
    --rust: #c2573a;
    --amber: #e0862e;
    --rule-gold: #e09a50;
    --plum: #a8558a;
  }
  html, body {
    margin: 0;
    padding: 0;
    overflow: hidden;
    background: var(--paper);
  }
  .values-wall {
    display: block;
    width: 821px;
    height: 1200px;
  }
  .paper { fill: url(#paperTone); }
  .rule { stroke-width: 3; }
  .rule--gold { stroke: var(--rule-gold); }
  .rule--rust { stroke: var(--rust); }
  .value--stencil { font-family: "Stardos Stencil", "Courier New", monospace; font-weight: 700; fill: var(--teal); }
  .value--fine { font-family: "Cinzel", Georgia, serif; fill: var(--apricot); }
  .value--heavy { font-family: "Anton", Impact, sans-serif; fill: var(--rust); }
  .value--slab { font-family: "Alfa Slab One", Georgia, serif; fill: var(--amber); }
  .value--tech { font-family: "Share Tech", Arial, sans-serif; fill: var(--teal); }
  .value--script { font-family: "Lobster", cursive; fill: var(--plum); }
  .value--western { font-family: "Sancreek", Georgia, serif; fill: var(--apricot); }
  .value--saloon { font-family: "Rye", Georgia, serif; fill: var(--rust); }
  .motif--amber { fill: var(--amber); }
  .motif--rust { fill: var(--rust); }
</style>
</head>
<body>
<svg class="values-wall" viewBox="0 0 821 1200" xmlns="http://www.w3.org/2000/svg">
  <defs>
    <linearGradient id="paperTone" x1="0" y1="0" x2="1" y2="1">
      <stop offset="0" stop-color="#f3f3f3"/>
      <stop offset="1" stop-color="#e6e6e6"/>
    </linearGradient>
  </defs>
  <rect class="paper" width="821" height="1200"/>

  <!-- Value 1 -->
  <line class="rule rule--gold" x1="117" y1="71" x2="695" y2="71"/>
  <text class="value--stencil" x="117" y="150" font-size="86" textLength="602" lengthAdjust="spacingAndGlyphs">STOP. THINK.</text>
  <text class="value--stencil" x="113" y="208" font-size="48" textLength="599" lengthAdjust="spacingAndGlyphs">CHALLENGE THE NORM.</text>

  <line class="rule rule--gold" x1="117" y1="235" x2="380" y2="235"/>
  <line class="rule rule--gold" x1="412" y1="235" x2="695" y2="235"/>
  <ellipse class="motif--amber" cx="396" cy="248" rx="12" ry="16" role="img" aria-label="Small leaf ornament"/>

  <!-- Value 2 -->
  <text class="value--fine" x="117" y="328" font-size="78" textLength="280" lengthAdjust="spacingAndGlyphs">OUR</text>
  <text class="value--fine" x="117" y="366" font-size="26" textLength="280" lengthAdjust="spacingAndGlyphs">DETAIL IS</text>
  <text class="value--heavy" x="410" y="368" font-size="118" textLength="287" lengthAdjust="spacingAndGlyphs">OUR</text>
  <text class="value--heavy" x="120" y="455" font-size="84" textLength="580" lengthAdjust="spacingAndGlyphs">DIFFERENCE.</text>

  <line class="rule rule--rust" x1="117" y1="478" x2="368" y2="478"/>
  <line class="rule rule--rust" x1="448" y1="478" x2="695" y2="478"/>
  <rect class="motif--rust" x="376" y="471" width="64" height="14" rx="5" role="img" aria-label="Pointing hand illustration"/>

  <!-- Value 3 -->
  <rect class="motif--rust" x="62" y="507" width="56" height="14" rx="7" role="img" aria-label="Left scroll flourish ornament"/>
  <rect class="motif--rust" x="700" y="507" width="56" height="14" rx="7" role="img" aria-label="Right scroll flourish ornament"/>
  <text class="value--slab" x="129" y="532" font-size="34" textLength="564" lengthAdjust="spacingAndGlyphs">BEST INTENTIONS. ALWAYS.</text>

  <line class="rule rule--rust" x1="117" y1="566" x2="390" y2="566"/>
  <line class="rule rule--rust" x1="438" y1="566" x2="700" y2="566"/>
  <circle class="motif--amber" cx="414" cy="566" r="20" role="img" aria-label="Round smile badge"/>

  <!-- Value 4 -->
  <text class="value--tech" x="85" y="640" font-size="52" textLength="660" lengthAdjust="spacingAndGlyphs">TURN UP, TURN ON!</text>
  <text class="value--tech" x="93" y="705" font-size="52" textLength="635" lengthAdjust="spacingAndGlyphs">MAKE ..IT HAPPEN!</text>

  <line class="rule rule--gold" x1="117" y1="730" x2="380" y2="730"/>
  <line class="rule rule--gold" x1="446" y1="730" x2="706" y2="730"/>
  <rect class="motif--amber" x="394" y="714" width="38" height="30" rx="7" role="img" aria-label="Thumbs up icon"/>

  <!-- Value 5 -->
  <text class="value--script" x="117" y="786" font-size="56" textLength="595" lengthAdjust="spacingAndGlyphs">Support Like Family.</text>
  <text class="value--western" x="126" y="898" font-size="96" textLength="296" lengthAdjust="spacingAndGlyphs">PARTY</text>
  <text class="value--western" x="480" y="898" font-size="96" textLength="215" lengthAdjust="spacingAndGlyphs">LIKE</text>

  <line class="rule rule--rust" x1="126" y1="925" x2="430" y2="925"/>
  <line class="rule rule--rust" x1="478" y1="925" x2="706" y2="925"/>
  <rect class="motif--rust" x="436" y="832" width="36" height="108" rx="9" role="img" aria-label="Silhouette of a rock performer raising a hand"/>

  <text class="value--saloon" x="118" y="1033" font-size="92" textLength="614" lengthAdjust="spacingAndGlyphs">ROCKSTARS.</text>
  <line class="rule rule--rust" x1="120" y1="1057" x2="706" y2="1057"/>
</svg>
</body>
</html>
```